Web design for financial services

A modern web design of financial services (brokerage firm)
Req.s and technology tags :
- Very mobile friendly.
- One paged with some inner pages.
- Animated sticky header .
- Member login area for e-trade.
- Support RTL language.
- HTML & CSS.

The logo will be Home link
• MPTR :
WHO WE ARE
Content :
i) Board of Directors
ii) Mission Statement
iii) Corporate Values
iv) Regulations
• Financial Services :
WHAT WE DO
Content:
i) Electronic trading
ii) Trading desk
iii) Institutional
iv) Investors Education
• News
• Market Tools
• Forms---- opens new page
• Careers---- opens new page
• Contact Us----opens new page

The website is :
http://www.mptr-doha-example.com/

The logo need some changes to be more modern and impressively , but with keeping same structure .

Some related websites :
https://www.lv-bourse.example/

financial market

Financial Service

Coded - Design and coding required

2 page

• same fonts of http://www.kwdholdings.example/

• - Very mobile friendly.
• - One paged with some inner pages.
• - Animated sticky header .
• - Member login area for e-trade.
• - Support RTL language.
• - HTML & CSS.
• Slider , some Qatari theme,
• i like the video inside the home page
• ex :http://www.kwdholdings.example/

```html
<!DOCTYPE html>
<html lang="en">
<head>
<meta charset="utf-8">
<title>MPTR – Forms</title>
<link href="https://fonts.googleapis.com/css2?family=Open+Sans:ital,wght@0,400;0,600;0,700;1,400&display=swap" rel="stylesheet">
<style>
:root{
  --brand:#9b2421;
  --ink:#1c1c1c;
  --text:#444;
  --muted:#777;
  --field:#e8e8e8;
  --field-line:#d6d6d6;
  --panel:#e6e6e6;
  --footer:#000;
  --white:#fff;
}
*{box-sizing:border-box;margin:0;padding:0}
html,body{width:1200px;height:2493px;overflow:hidden}
body{position:relative;background:var(--white);font-family:"Open Sans",Arial,sans-serif;color:var(--text)}
a{color:inherit;text-decoration:none}

/* Header */
.site-header{position:absolute;left:0;top:0;width:1200px;height:120px;background:var(--white);z-index:2}
.brand{position:absolute;left:76px;top:38px;display:flex;align-items:center;gap:12px}
.brand-mark{width:34px;height:34px;border:5px solid var(--brand)}
.brand-name{font-size:40px;font-weight:700;color:var(--ink);letter-spacing:-1px;line-height:1}
.etrade-btn{position:absolute;left:926px;top:27px;width:101px;height:26px;background:var(--brand);color:var(--white);font-size:10px;font-weight:700;display:flex;align-items:center;justify-content:center;gap:6px;border-radius:2px}
.etrade-btn svg{width:10px;height:10px}
.lang-btn{position:absolute;left:1037px;top:27px;width:87px;height:26px;border:1px solid #999;border-radius:2px;font-size:9px;color:var(--ink);display:flex;align-items:center;justify-content:center;gap:6px}
.lang-flag{width:13px;height:9px;background:#2a3f8f}
.main-nav{position:absolute;right:76px;top:80px;display:flex;gap:36px;font-size:12px;font-weight:700;color:var(--ink)}
.main-nav .active{color:var(--brand)}

/* Hero */
.hero{position:absolute;left:0;top:120px;width:1200px;height:545px;background:linear-gradient(120deg,#2a2a2c 0%,#4a3a30 35%,#6b5a4c 55%,#3a3a40 80%,#222 100%)}
.hero-shade{position:absolute;inset:0;background:rgba(0,0,0,.35)}
.hero-title{position:absolute;left:0;right:0;top:180px;text-align:center;font-size:64px;font-weight:700;color:var(--white);letter-spacing:1px}
.hero-cut{position:absolute;left:0;bottom:0;width:1200px;height:146px}

/* Sidebar */
.side-title{position:absolute;left:161px;top:700px;font-size:15px;font-weight:700;color:var(--brand)}
.side-rule{position:absolute;left:161px;top:734px;width:47px;height:4px;background:var(--ink)}
.side-link{position:absolute;left:161px;top:759px;font-size:11px;font-weight:700;color:var(--ink)}
.video-thumb{position:absolute;left:161px;top:816px;width:185px;height:140px;background:linear-gradient(180deg,#9fb6cc 0%,#7d93a8 55%,#4d5f6e 100%)}
.video-play{position:absolute;left:68px;top:46px;width:48px;height:48px}
.news-panel{position:absolute;left:161px;top:969px;width:185px;height:838px;background:var(--panel);padding:22px 16px}
.news-heading{font-size:13px;font-weight:700;color:var(--ink);margin-bottom:18px}
.news-item{margin-bottom:20px}
.news-date{font-size:9px;font-style:italic;color:var(--muted);margin-bottom:6px}
.news-text{font-size:11.5px;line-height:18px;color:var(--ink)}
.news-more{display:block;margin-top:6px;font-size:10px;font-style:italic;color:var(--brand)}

/* Content */
.content{position:absolute;left:381px;top:697px;width:658px}
.content-title{font-size:21px;font-weight:700;color:var(--brand)}
.content-sub{margin-top:14px;font-size:13px;font-style:italic;color:var(--ink)}
.content p{font-size:11px;line-height:20px;color:var(--text)}
.p1{margin-top:22px}
.p2,.p3{margin-top:22px}

.form-head{position:absolute;left:381px;top:1168px;width:658px;height:45px;border-bottom:1px solid var(--field-line)}
.form-title{font-size:21px;font-weight:700;color:var(--brand)}
.form-note{position:absolute;right:0;top:10px;font-size:11px;font-style:italic;color:var(--muted)}
.field{position:absolute;width:321px}
.field label{display:block;font-size:11.5px;color:var(--ink);margin-bottom:6px}
.field label span{color:var(--brand)}
.field .box{display:block;width:100%;height:38px;background:var(--field);border:1px solid var(--field-line)}
.field .select{display:flex;align-items:center;justify-content:space-between;padding:0 12px;font-size:11.5px;color:var(--ink)}
.field .area{height:150px}
.col-l{left:381px}.col-r{left:718px}
.submit-btn{position:absolute;left:381px;top:1740px;width:113px;height:37px;background:var(--brand);color:var(--white);font-size:13px;font-weight:700;display:flex;align-items:center;justify-content:center;border-radius:2px}

/* Skyline band */
.skyline{position:absolute;left:0;top:1905px;width:1200px;height:333px;background:linear-gradient(180deg,#fff 0%,#f1dcda 25%,#c47d77 60%,#9b3f3a 100%)}

/* Footer */
.site-footer{position:absolute;left:0;top:2238px;width:1200px;height:255px;background:var(--footer);color:var(--white);text-align:center}
.footer-brand{position:absolute;left:0;right:0;top:52px;display:flex;justify-content:center;align-items:center;gap:10px}
.footer-brand .brand-mark{width:28px;height:28px;border:4px solid var(--white)}
.footer-brand .brand-name{font-size:30px;color:var(--white)}
.footer-nav{position:absolute;left:0;right:0;top:126px;font-size:13px;font-weight:700}
.footer-nav .sep{margin:0 14px}
.footer-copy{position:absolute;left:0;right:0;top:160px;font-size:10px}
.footer-social{position:absolute;left:0;right:0;top:193px;display:flex;justify-content:center;gap:10px}
.footer-social span{width:25px;height:25px;border:1px solid var(--white);border-radius:50%}
</style>
</head>
<body>

<header class="site-header">
  <a class="brand" href="#"><span class="brand-mark"></span><span class="brand-name">MPTR</span></a>
  <a class="etrade-btn" href="#"><svg viewBox="0 0 10 10"><rect x="1" y="1" width="8" height="8" fill="none" stroke="#fff" stroke-width="1.2"/><path d="M3 5h5M6 3l2 2-2 2" fill="none" stroke="#fff" stroke-width="1.2"/></svg>MPTR E-TRADE</a>
  <a class="lang-btn" href="#"><span class="lang-flag"></span>ENGLISH <svg width="7" height="5" viewBox="0 0 7 5"><path d="M1 1l2.5 2.5L6 1" fill="none" stroke="#333"/></svg></a>
  <nav class="main-nav">
    <a href="#">MPTR</a><a href="#">FINANCIAL SERVICE</a><a href="#">NEWS</a><a href="#">MARKET TOOL</a><a class="active" href="#">FORMS</a><a href="#">CAREERS</a><a href="#">CONTACT US</a>
  </nav>
</header>

<section class="hero">
  <div class="hero-shade" role="img" aria-label="Photo of a person reviewing financial charts beside a laptop"></div>
  <h1 class="hero-title">FORMS</h1>
  <svg class="hero-cut" viewBox="0 0 1200 146" preserveAspectRatio="none"><polygon points="0,75 394,0 1200,146 0,146" fill="#fff"/></svg>
</section>

<aside>
  <div class="side-title">FORMS</div>
  <div class="side-rule"></div>
  <a class="side-link" href="#">COMPLAINTS</a>
  <div class="video-thumb" role="img" aria-label="Video still of the Doha city skyline">
    <svg class="video-play" viewBox="0 0 48 48"><circle cx="24" cy="24" r="22" fill="rgba(0,0,0,.45)" stroke="#fff" stroke-width="3"/><path d="M19 14l14 10-14 10z" fill="#fff"/></svg>
  </div>
  <div class="news-panel">
    <div class="news-heading">MARKET NEWS</div>
    <div class="news-item"><div class="news-date">February 23 2017</div><div class="news-text">Sed ut perspiciatis unde omnis iste natus error sit voluptatem accusantium dolore</div><a class="news-more" href="#">Read More</a></div>
    <div class="news-item"><div class="news-date">February 23 2017</div><div class="news-text">Sed ut perspiciatis unde omnis iste natus error sit voluptatem accusantium dolore</div><a class="news-more" href="#">Read More</a></div>
    <div class="news-item"><div class="news-date">February 23 2017</div><div class="news-text">Sed ut perspiciatis unde omnis iste natus error sit voluptatem accusantium dolore</div><a class="news-more" href="#">Read More</a></div>
    <div class="news-item"><div class="news-date">February 23 2017</div><div class="news-text">Sed ut perspiciatis unde omnis iste natus error sit voluptatem accusantium dolore</div><a class="news-more" href="#">Read More</a></div>
    <div class="news-item"><div class="news-date">February 23 2017</div><div class="news-text">Sed ut perspiciatis unde omnis iste natus error sit voluptatem accusantium dolore</div><a class="news-more" href="#">Read More</a></div>
    <div class="news-item"><div class="news-date">February 23 2017</div><div class="news-text">Sed ut perspiciatis unde omnis iste natus error sit voluptatem accusantium dolore</div><a class="news-more" href="#">Read More</a></div>
  </div>
</aside>

<main>
  <article class="content">
    <h2 class="content-title">Filling a Complaint</h2>
    <div class="content-sub">What should I do if I have a complaint?</div>
    <p class="p1">Sed ut perspiciatis unde omnis iste natus error sit voluptatem accusantium doloremque laudantium, totam rem aperiam, eaque ipsa quae ab illo inventore veritatis et quasi architecto beatae vitae dicta sunt explicabo. Nemo enim ipsam voluptatem quia voluptas sit aspernatur aut odit aut fugit, sed quia consequuntur magni dolores eos qui ratione voluptatem sequi nesciunt neque porro quisquam est.</p>
    <p class="p2">Sed ut perspiciatis unde omnis iste natus error sit voluptatem accusantium doloremque laudantium, totam rem aperiam, eaque ipsa quae ab illo inventore veritatis et quasi architecto beatae vitae dicta sunt explicabo, nemo enim ipsam voluptatem quia voluptas sit aspernatur.</p>
    <p class="p3">Sed ut perspiciatis unde omnis iste natus error sit voluptatem accusantium doloremque laudantium, totam rem aperiam, eaque ipsa quae ab illo inventore veritatis et quasi architecto beatae vitae dicta sunt explicabo. Nemo enim ipsam voluptatem quia voluptas sit aspernatur aut odit aut fugit, sed quia consequuntur magni dolores eos qui ratione voluptatem sequi nesciunt neque porro quisquam est. Ut enim ad minima veniam, quis nostrum exercitationem ullam corporis suscipit laboriosam, nisi ut aliquid ex ea commodi consequatur. Quis autem vel eum iure reprehenderit qui in ea voluptate velit esse quam nihil molestiae consequatur, vel illum qui dolorem eum fugiat quo voluptas nulla pariatur.</p>
  </article>

  <div class="form-head">
    <h2 class="form-title">Client Complaints Form</h2>
    <span class="form-note">* mandatory fields</span>
  </div>

  <div class="field col-l" style="top:1232px"><label>Complaint Type <span>*</span></label><div class="box select">Choose one<svg width="10" height="6" viewBox="0 0 10 6"><path d="M0 0h10L5 6z" fill="#222"/></svg></div></div>
  <div class="field col-r" style="top:1232px"><label>Email Address <span>*</span></label><div class="box"></div></div>
  <div class="field col-l" style="top:1307px"><label>Phone <span>*</span></label><div class="box"></div></div>
  <div class="field col-r" style="top:1307px"><label>Subject <span>*</span></label><div class="box"></div></div>
  <div class="field col-l" style="top:1388px"><label>Account Name <span>*</span></label><div class="box"></div></div>
  <div class="field col-r" style="top:1388px"><label>Account Number <span>*</span></label><div class="box"></div></div>
  <div class="field col-l" style="top:1468px"><label>Order/Ticket Number <span>*</span></label><div class="box"></div></div>
  <div class="field col-r" style="top:1468px"><label>Date and time of the order/ticket <span>*</span></label><div class="box"></div></div>
  <div class="field col-l" style="top:1551px;width:658px"><label>Description of complaint <span>*</span></label><div class="box area"></div></div>
  <a class="submit-btn" href="#">SUBMIT</a>
</main>

<div class="skyline" role="img" aria-label="Illustrated Doha skyline in shades of red"></div>

<footer class="site-footer">
  <div class="footer-brand"><span class="brand-mark"></span><span class="brand-name">MPTR</span></div>
  <nav class="footer-nav">
    <a href="#">MPTR</a><span class="sep">|</span><a href="#">FINACIAL SERVICE</a><span class="sep">|</span><a href="#">NEWS</a><span class="sep">|</span><a href="#">MARKET TOOL</a><span class="sep">|</span><a href="#">CAREERS</a><span class="sep">|</span><a href="#">CONTACT US</a>
  </nav>
  <div class="footer-copy">©2017. All Rights Reserved | MPTR Qatar | Copyright, Legal and Privacy Statement.Disclaimers and Legal Information</div>
  <div class="footer-social"><span></span><span></span><span></span><span></span><span></span></div>
</footer>

</body>
</html>
```